Business Card for brovaLINK

Create a Business Card with an existing logo for brovaLINK AG. We are a Information Technology company that does consulting and developing SW to automate business processes. The main colors are given from the logo.

Industry/Entity Type

Business

Requirements
Nice to have
• we use a a font style Century Gothic in our documents

```html
<!DOCTYPE html>
<html lang="en">
<head>
<meta charset="utf-8">
<title>brovaLINK business card</title>
<link href="https://fonts.googleapis.com/css2?family=Oswald:wght@500&family=Questrial&display=swap" rel="stylesheet">
<style>
  :root {
    --stage: #8c8c8c;
    --card-dark: #1d1d1d;
    --card-light: #ffffff;
    --green: #7cc425;
    --green-light: #a9e04a;
    --text-light: #f2f2f2;
    --text-dark: #1a1a1a;
  }
  * { box-sizing: border-box; margin: 0; padding: 0; }
  html, body { width: 1200px; height: 904px; overflow: hidden; }
  body {
    background: var(--stage);
    font-family: "Questrial", "Century Gothic", sans-serif;
    position: relative;
  }
  .card {
    position: absolute;
    top: 152px;
    width: 340px;
    height: 600px;
    overflow: hidden;
    box-shadow: 0 14px 30px rgba(0,0,0,.35);
  }
  .card--back { left: 175px; background: var(--card-dark); }
  .card--front { left: 685px; background: var(--card-light); }

  .top-strip {
    position: absolute; left: 0; top: 0; width: 100%; height: 18px;
    background: linear-gradient(90deg, var(--green), var(--green-light));
  }

  /* back side */
  .holder { position: absolute; left: 0; top: 100px; display: flex; align-items: center; }
  .holder__marker { width: 22px; height: 44px; background: var(--green); }
  .holder__text { margin-left: 14px; color: var(--text-light); }
  .holder__name { font-family: "Oswald", sans-serif; font-weight: 500; font-size: 26px; letter-spacing: 1px; line-height: 1; }
  .holder__role { font-size: 13px; letter-spacing: 1.5px; margin-top: 4px; }

  .contacts { position: absolute; left: 36px; top: 212px; list-style: none; }
  .contacts li { display: flex; align-items: center; height: 30px; color: var(--text-light); font-size: 13px; letter-spacing: .4px; white-space: nowrap; }
  .contacts .icon {
    width: 22px; height: 22px; border-radius: 4px; background: var(--green);
    display: flex; align-items: center; justify-content: center; margin-right: 10px; flex: none;
  }
  .contacts svg { width: 14px; height: 14px; }

  .light-foot {
    position: absolute; left: 0; bottom: 0; width: 100%; height: 160px;
    background: var(--card-light); border-top: 6px solid var(--green);
    display: flex; align-items: center; justify-content: center;
  }

  /* front side */
  .logo-area { position: absolute; left: 0; top: 18px; width: 100%; height: 380px; display: flex; align-items: center; justify-content: center; }
  .dark-foot {
    position: absolute; left: 0; bottom: 0; width: 100%; height: 202px;
    background: var(--card-dark); border-top: 6px solid var(--green);
    display: flex; align-items: center; justify-content: center;
  }
  .website { color: var(--text-light); font-size: 16px; letter-spacing: 1px; margin-top: 40px; }

  .brand { display: flex; align-items: center; gap: 10px; }
  .brand__dot { width: 38px; height: 38px; border-radius: 50%; background: var(--green); }
  .brand__name { font-size: 34px; color: var(--text-dark); letter-spacing: .5px; }
  .brand--small .brand__dot { width: 30px; height: 30px; }
  .brand--small .brand__name { font-size: 28px; }
</style>
</head>
<body>

<section class="card card--back" aria-label="Card back with contact details">
  <div class="top-strip"></div>
  <div class="holder">
    <div class="holder__marker"></div>
    <div class="holder__text">
      <div class="holder__name">LENA MORROW</div>
      <div class="holder__role">GENERAL MANAGER</div>
    </div>
  </div>

  <ul class="contacts">
    <li><span class="icon"><svg viewBox="0 0 16 16" fill="#1d1d1d"><path d="M4 1l2.5 3-1.5 2c1 2 2.5 3.5 4.5 4.5l2-1.5 3 2.5-1.5 2.5C7 15 1 9 1.5 2.5z"/></svg></span>012 555 0148</li>
    <li><span class="icon"><svg viewBox="0 0 16 16" fill="#1d1d1d"><rect x="4" y="1" width="8" height="14" rx="1.5"/><rect x="5.5" y="3" width="5" height="8" fill="#7cc425"/></svg></span>012 555 0149</li>
    <li><span class="icon"><svg viewBox="0 0 16 16" fill="#1d1d1d"><rect x="4" y="1" width="8" height="5"/><rect x="1" y="6" width="14" height="7" rx="1"/><rect x="4" y="10" width="8" height="5" fill="#7cc425" stroke="#1d1d1d"/></svg></span>012 555 0150</li>
    <li><span class="icon"><svg viewBox="0 0 16 16" fill="none" stroke="#1d1d1d" stroke-width="1.6"><rect x="1.5" y="3.5" width="13" height="9"/><path d="M1.5 3.5l6.5 5 6.5-5"/></svg></span>lena@brovalink.ch</li>
    <li><span class="icon"><svg viewBox="0 0 16 16" fill="none" stroke="#1d1d1d" stroke-width="1.4"><circle cx="8" cy="8" r="6.5"/><ellipse cx="8" cy="8" rx="3" ry="6.5"/><path d="M1.5 8h13"/></svg></span>www.brovalink.ch</li>
    <li><span class="icon"><svg viewBox="0 0 16 16" fill="#1d1d1d"><path d="M8 1a5 5 0 0 1 5 5c0 4-5 9-5 9S3 10 3 6a5 5 0 0 1 5-5z"/><circle cx="8" cy="6" r="2" fill="#7cc425"/></svg></span>12, 4th floor, Seefeld Allee ZH</li>
  </ul>

  <div class="light-foot">
    <div class="brand brand--small">
      <span class="brand__dot"></span>
      <span class="brand__name">brovaLINK</span>
    </div>
  </div>
</section>

<section class="card card--front" aria-label="Card front with brand name">
  <div class="top-strip"></div>
  <div class="logo-area">
    <div class="brand">
      <span class="brand__dot"></span>
      <span class="brand__name">brovaLINK</span>
    </div>
  </div>
  <div class="dark-foot">
    <span class="website">www.brovalink.ch</span>
  </div>
</section>

</body>
</html>
```